Harrow Hide Revival Product Label

We need a design for a label to be used on bottles of leather cleaner and conditioner products that will be used in curated kits. We would like it to incorporate our business logo as well as have an area that we can fill in later with the appropriate product name as needed. We would like to see designs that use shades of brown, but we are open to other colors often seen in leather. I am including the Harrow Hide business Logo below, however again we would prefer to have the label in various shades of browns, rather than the red and grey, more like the mock-up that I am also attaching.

*** I am attaching examples of the types of bottles that will be used. They vary in size from 8 oz to 16 oz. if you are designing a label for a spray bottle they are from 16-32 oz. ***

```html
<!DOCTYPE html>
<html lang="en">
<head>
<meta charset="utf-8">
<title>Harrow Hide Revival – Leather Cleaner Label</title>
<link rel="stylesheet" href="https://fonts.googleapis.com/css2?family=Oswald:wght@500;600&family=Kaushan+Script&display=swap">
<style>
  :root {
    --backdrop: #a7b1bd;
    --band-edge: #5b3315;
    --cream: #ffffff;
    --ink: #1e1a18;
    --badge-yellow: #f2c31a;
    --warning-tint: #e9d7c3;
  }
  * { margin: 0; padding: 0; box-sizing: border-box; }
  html, body { width: 1200px; height: 834px; overflow: hidden; }
  body {
    background: var(--backdrop);
    font-family: "Oswald", "Arial Narrow", sans-serif;
  }
  .label {
    position: absolute;
    left: 369px; top: 35px;
    width: 462px; height: 765px;
    border-radius: 14px;
    overflow: hidden;
  }
  .label-art { position: absolute; inset: 0; width: 100%; height: 100%; display: block; }
  .brand {
    position: absolute; left: 37px; top: 100px;
    display: flex; align-items: center; gap: 12px;
  }
  .brand-dot {
    width: 40px; height: 40px; border-radius: 50%;
    background: var(--ink);
  }
  .brand-name {
    font-family: "Oswald", sans-serif; font-weight: 500;
    font-size: 28px; letter-spacing: 1px; color: var(--ink);
    text-transform: uppercase;
  }
  .product-name {
    position: absolute; left: 26px; top: 205px;
    font-family: "Kaushan Script", cursive;
    font-weight: 400;
    color: var(--cream);
    font-size: 94px; line-height: 100px;
    text-shadow: 3px 4px 0 rgba(40,20,8,0.75);
    white-space: nowrap;
  }
  .product-name span { display: block; }
  .product-name .line-two { padding-left: 78px; }
  .badge {
    position: absolute; left: 279px; top: 522px;
    width: 156px; height: 58px;
    border-radius: 50%;
    background: var(--badge-yellow);
    border: 3px solid var(--ink);
    display: flex; align-items: center; justify-content: center;
    text-align: center;
    font-weight: 600; font-size: 20px; line-height: 21px;
    color: var(--cream);
    -webkit-text-stroke: 0.6px var(--ink);
    text-shadow: 1px 1px 0 var(--ink);
  }
  .warning {
    position: absolute; left: 28px; top: 624px; width: 200px;
    font-size: 11px; line-height: 13px; text-align: center;
    color: var(--warning-tint);
  }
  .volume {
    position: absolute; left: 0; right: 0; top: 683px;
    text-align: center; font-size: 21px; font-weight: 500;
    color: var(--cream);
  }
</style>
</head>
<body>
  <section class="label">
    <svg class="label-art" viewBox="0 0 462 765">
      <defs>
        <radialGradient id="hideTone" cx="55%" cy="35%" r="75%">
          <stop offset="0" stop-color="#c47d43"/>
          <stop offset="0.6" stop-color="#a8642f"/>
          <stop offset="1" stop-color="#7f4a20"/>
        </radialGradient>
        <linearGradient id="bandTone" x1="0" y1="0" x2="0" y2="1">
          <stop offset="0" stop-color="#8a5528"/>
          <stop offset="1" stop-color="#6a3b17"/>
        </linearGradient>
      </defs>
      <rect class="hide-texture" role="img" aria-label="Close-up of brown grained leather texture" width="462" height="765" fill="url(#hideTone)"/>
      <path class="band-edge" d="M0 505 C 110 470, 200 455, 300 470 C 370 480, 420 470, 462 455 L462 765 L0 765 Z" fill="var(--band-edge)"/>
      <path class="band" d="M0 520 C 110 488, 200 475, 300 490 C 370 500, 420 490, 462 476 L462 765 L0 765 Z" fill="url(#bandTone)"/>
    </svg>

    <div class="brand">
      <div class="brand-dot"></div>
      <div class="brand-name">Harrow Hide Revival</div>
    </div>

    <h1 class="product-name"><span>Leather</span><span class="line-two">Cleaner</span></h1>

    <div class="badge">Makes Leather<br>Last Longer</div>

    <p class="warning">WARNING: Possible Eye or Skin Irritant<br>See "WARNING" on the back label</p>

    <p class="volume">16 US FL. OZ 473 ML</p>
  </section>
</body>
</html>
```